Webdesign für Sexualpädagogik
Zielgruppe
- Sexualpädagogik, Beratung und Sexualtherapie
- Vorträge und Seminare für Unternehmen / Institutionen Vorträge Sexualität in der Pflege / im Alter / Grenzen wahrnehmen
- Wechseljahreberatung, Beratung in der Lebensmitte
- ZIelgruppe: Menschen, die sich weiternetwickeln möchten, die Problme mit ihrer Sexualität haben, Paare, Jugendliche
letztes Interview in der Zeitung: https://www.talpost-beispiel.ch/nachrichtenblatt/zeitung/frontal-interview/sexualitaet-hoert-nicht-beim-eintritt-ins-spital-auf/
Aufgabenstellung
- bestehende Internetseite siehe unten: Schrift ist Especial Key von Tauwerk Mitte
- auf dem Briefpapier bisher noch der Fachbuchhandel und Onlinhandel, aber beides nicht mehr
- Bilder zum Thema bereist vorhanden
- für Werbeflyer habe ich die Therapie in dunkelblau gehalten udn in der sexualpädagogik in hellblau
der kramkiste wird aus der website entfernet

```html
<!DOCTYPE html>
<html lang="de">
<head>
<meta charset="utf-8">
<title>Tauwerk Mitte – Fachstelle für Sexualpädagogik</title>
<link href="https://fonts.googleapis.com/css2?family=Roboto:ital,wght@0,300;0,400;0,500;1,500&display=swap" rel="stylesheet">
<style>
:root{
  --blue:#0a4dab;
  --blue-soft:#c9dcf5;
  --blue-line:#9ec0ec;
  --ink:#1b1b1b;
  --grey:#555;
  --panel:#f4f4f4;
  --white:#fff;
}
*{margin:0;padding:0;box-sizing:border-box}
html,body{width:714px;height:1200px;overflow:hidden;background:var(--white);font-family:'Roboto',Arial,sans-serif;color:var(--ink)}
.page{position:relative;width:714px;height:1200px}
.abs{position:absolute}
.sidebar{left:0;top:0;width:40px;height:1200px;background:var(--blue)}
.sidebar-name{position:absolute;left:20px;top:165px;transform:translate(-50%,-50%) rotate(-90deg);color:var(--white);font-size:17px;font-weight:400;white-space:nowrap;letter-spacing:1px}
.brand{left:200px;top:10px;width:350px;text-align:center}
.brand-mark{position:absolute;left:5px;top:6px;width:34px;height:34px;border-radius:50%;background:var(--blue)}
.brand-name{font-size:27px;font-weight:500;color:var(--blue);letter-spacing:1px;line-height:34px;padding-left:40px}
.brand-sub{font-size:7.8px;font-style:italic;font-weight:500;margin-top:6px;line-height:13px}
.brand-sub em{color:var(--blue)}
.nav{left:89px;top:88px;width:536px;height:26px;background:var(--blue);display:flex;justify-content:space-around;align-items:center;padding:0 28px}
.nav a{color:var(--white);font-size:8px;font-weight:500;text-decoration:none}
.hero{left:90px;top:114px;width:535px;height:207px;background:linear-gradient(120deg,#7d8a3a 0%,#c85a33 25%,#8b98a6 45%,#d2a98b 60%,#2a9cc4 75%,#4e7a2e 100%)}
.hero-band{left:180px;top:248px;width:375px;height:24px;background:rgba(255,255,255,.15)}
.hero-title{left:90px;top:248px;width:535px;text-align:center;color:var(--white);font-size:16px;font-weight:300;line-height:24px}
.card{top:330px;height:151px;width:263px;padding:24px 18px 0;text-align:center}
.card-therapy{left:90px;background:linear-gradient(135deg,#2c6cc0,#1b58b0);color:var(--white)}
.card-edu{left:362px;background:linear-gradient(135deg,#c6d8f2,#d8e5f7);color:var(--ink)}
.card h3{font-size:12.5px;font-weight:400;margin-bottom:12px}
.card p{font-size:8px;line-height:12.5px;text-align:left;font-weight:400}
.card-edu p{font-weight:300}
.btn{display:inline-block;margin-top:18px;font-size:8px;padding:3px 6px}
.card-therapy .btn{background:var(--white);color:var(--blue)}
.card-edu .btn{background:var(--blue);color:var(--white)}
.section-title{left:89px;width:536px;text-align:center;color:var(--blue);font-size:15px;font-weight:400}
.section-title::after{content:"";display:block;width:45px;height:1.5px;background:var(--blue-line);margin:2px auto 0}
.about{left:89px;top:539px;width:536px;border-left:2.5px solid var(--blue);padding-left:18px;font-size:7.9px;line-height:13.4px;font-weight:300}
.service{top:649px;width:161px;height:128px;border:1px solid #e3e3e3;border-bottom:4px solid var(--blue);text-align:center}
.service-icon{width:56px;height:66px;margin:17px auto 0;border-radius:28px 28px 10px 10px;background:var(--blue)}
.service-label{font-size:10.5px;margin-top:12px}
.service.is-active{background:var(--blue);color:var(--white);border-color:var(--blue)}
.service.is-active .service-icon{background:#3d72c2}
.testimonial{left:89px;top:803px;width:535px;height:146px;background:var(--panel);border:1px solid #e6e6e6}
.arrow{font-size:12px;color:var(--ink)}
.portrait{left:143px;top:834px;width:82px;height:88px;border-radius:50%;background:linear-gradient(160deg,#e8cdb5,#b08462)}
.quote-mark{left:220px;top:842px;font-size:42px;font-weight:500;color:var(--blue);line-height:42px}
.stars{left:264px;top:828px;color:var(--blue);font-size:9px;letter-spacing:1px}
.reviewer{left:265px;top:846px;font-size:8px;letter-spacing:1.5px;color:var(--grey);font-weight:500}
.review{left:265px;top:862px;width:325px;font-size:7px;line-height:10.5px;color:var(--grey);font-weight:300}
.review-line{left:265px;top:916px;width:13px;height:1.5px;background:var(--blue)}
.col-title{font-size:14px;color:var(--blue);font-weight:400}
.news{left:91px;top:1000px;width:280px;font-size:7.3px;line-height:10.7px;font-weight:300;color:var(--ink)}
.news b{font-weight:400}
.news p+p{margin-top:13px}
.seminars{left:417px;top:998px;width:207px;height:106px;background:var(--blue);color:var(--white);padding:15px 23px;font-size:8.5px;line-height:15.5px}
.seminars .big{font-size:10.5px}
.footer{left:88px;top:1120px;width:536px;height:32px;background:var(--blue);display:flex;align-items:center;padding:0 11px;gap:14px}
.footer a{color:var(--white);font-size:7px;text-decoration:none}
.footer .legal{margin-left:auto}
.social{left:540px;top:1165px;font-size:7px;color:var(--blue);display:flex;gap:10px}
</style>
</head>
<body>
<div class="page">
  <aside class="abs sidebar"><span class="sidebar-name">Tauwerk Mitte</span></aside>

  <header class="abs brand">
    <span class="brand-mark"></span>
    <div class="brand-name">Tauwerk Mitte</div>
    <div class="brand-sub">Fachstelle Fur <em>Sexualpadagogik, Beratung</em> und <em>Therapie</em><br>Mara Velten</div>
  </header>

  <nav class="abs nav">
    <a href="#">HOME</a><a href="#">ÜBER MICH</a><a href="#">GÄSTEBUCH</a><a href="#">NEWSLETTER</a><a href="#">PREISE</a><a href="#">KONTAKT</a>
  </nav>

  <div class="abs hero" role="img" aria-label="Foto: Pflegerin lächelt einem älteren Mann im Garten zu"></div>
  <div class="abs hero-band"></div>
  <h1 class="abs hero-title">Sexualpädagogik, Beratung und Sexualtherapie</h1>

  <section class="abs card card-therapy" role="img" aria-label="Hintergrundfoto Therapie, dunkelblau getönt">
    <h3>Therapie</h3>
    <p>Lorem ipsum dolor sit amet, consectetuer adipiscing elit. Class aptent taciti sociosqu ad litora torquent per conubia nostra, per inceptos hymenaeos.</p>
    <span class="btn">Weiterlesen</span>
  </section>
  <section class="abs card card-edu" role="img" aria-label="Hintergrundfoto Sexualpädagogik, hellblau getönt">
    <h3>Sexualpädagogik</h3>
    <p>Sex education is the educational work with girls and boys on their questions about love, feelings and sexuality as well as gender aspects.</p>
    <span class="btn">Weiterlesen</span>
  </section>

  <h2 class="abs section-title" style="top:500px">WER WIR SIND</h2>
  <p class="abs about">Lorem ipsum dolor sit amet, consectetuer adipiscing elit. Class aptent taciti sociosqu ad litora torquent per conubia nostra, per inceptos hymenaeos. Nulla non arcu lacinia neque faucibus fringilla. Ut enim ad minim veniam, quis nostrud exercitation ullamco laboris nisi ut aliquip ex ea commodo consequat. Nam quis nulla. Ut tempus purus at lorem. Duis aute irure dolor in reprehenderit in voluptate velit esse cillum dolore eu fugiat nulla pariatur. Fusce wisi. Nullam lectus justo, vulputate eget mollis sed, tempor sed magna.</p>

  <h2 class="abs section-title" style="top:613px">WAS WIR TUN</h2>
  <div class="abs service" style="left:89px">
    <div class="service-icon" role="img" aria-label="Illustration: Kopf mit Geschlechtersymbol"></div>
    <div class="service-label">Sexualpädagogik</div>
  </div>
  <div class="abs service is-active" style="left:276px">
    <div class="service-icon" role="img" aria-label="Illustration: zwei Profile im Gespräch"></div>
    <div class="service-label">Sexualberatung / Sexualtherapie</div>
  </div>
  <div class="abs service" style="left:464px">
    <div class="service-icon" role="img" aria-label="Illustration: Beratungsgespräch am Tisch"></div>
    <div class="service-label">Wechseljahrberatung</div>
  </div>

  <section class="abs testimonial"></section>
  <span class="abs arrow" style="left:107px;top:871px">‹</span>
  <span class="abs arrow" style="left:599px;top:871px">›</span>
  <div class="abs portrait" role="img" aria-label="Porträtfoto der bewertenden Person"></div>
  <div class="abs quote-mark">“</div>
  <div class="abs stars">★★★★★</div>
  <div class="abs reviewer">JONAS HELLBERG</div>
  <p class="abs review">Lorem ipsum dolor sit amet, consectetuer adipiscing elit. Class aptent taciti sociosqu ad litora torquent per conubia nostra, per inceptos hymenaeos. Nulla non arcu lacinia neque faucibus fringilla. Ut enim ad minim veniam, quis nostrud exercitation ullamco laboris nisi ut aliquip ex ea commodo consequat. Nam quis nulla. Ut tempus purus at lorem.</p>
  <div class="abs review-line"></div>

  <h2 class="abs col-title" style="left:91px;top:970px">News</h2>
  <span class="abs arrow" style="left:344px;top:972px">‹</span>
  <span class="abs arrow" style="left:357px;top:972px;color:var(--blue)">›</span>
  <div class="abs news">
    <p><b>"I make everyone a good li ...</b><br>Talfeld / Where others blush, she speaks plain text. Mara Velten is a sex pedagogue and says: "Sex is learnable." - - By Lea Brunner - Nina Roth - - Which one is ... [more]</p>
    <p><b>"Mail's to info@tauwerk-mitte.ch</b><br>Unfortunately in the last week many mails of Tauwerk Mitte were devoured by the spam filter. - - I apologize for the inconvenience. Maybe just ... [more]</p>
  </div>

  <h2 class="abs col-title" style="left:417px;top:970px">Nächste Seminare</h2>
  <div class="abs seminars">
    xxxxxxxxxxxxxxxxxxxxxxxxx<br>xxxxxxxxxxxxxxxx<br>xxxxxxxxxxxxxxxxxxxxx<br>
    <span class="big">Daten: Nov, 13, 2018<br>Ruf uns jetzt an: 123-456-7890</span>
  </div>

  <footer class="abs footer">
    <a href="#">Impressum</a><a href="#">Lageplan</a><a href="#">News</a><a href="#">Nächste Seminare</a><a href="#">Kontakt</a><a href="#">über Mara Velten / Tauwerk Mitte</a>
    <a class="legal" href="#">Datenschutz | Terms &amp; Bedingungen</a>
  </footer>
  <div class="abs social"><span>Kontaktnetz</span><span>Freundeskreis</span></div>
</div>
</body>
</html>
```